I'm looking for a smart new design for business cards

Industry/Entity Type

Commercial Electrical

Contact Information for Business Card

Logo, name, email, position, website QR

Requirements
Nice to have
• Logo embedded behind the text side

```html
<!DOCTYPE html>
<html lang="en">
<head>
<meta charset="utf-8">
<title>Voltline Commercial Power – Business Card</title>
<link rel="stylesheet" href="https://fonts.googleapis.com/css2?family=Montserrat:wght@400;500;700;800&display=swap">
<style>
  :root {
    --stage: #9a9a9a;
    --navy: #2a2a72;
    --navy-soft: #7f86c4;
    --red: #e0202e;
    --ink: #333333;
    --paper: #ffffff;
  }
  * { box-sizing: border-box; margin: 0; padding: 0; }
  html, body { width: 1200px; height: 1108px; overflow: hidden; }
  body {
    background: var(--stage);
    font-family: "Montserrat", Arial, sans-serif;
    position: relative;
  }
  .card {
    position: absolute;
    left: 242px;
    width: 716px;
    height: 410px;
    border-radius: 30px;
    overflow: hidden;
  }
  .card--front { top: 119px; background: var(--navy); }
  .card--back { top: 581px; background: var(--paper); }

  .front-mark {
    position: absolute;
    inset: 0;
    display: flex;
    align-items: center;
    justify-content: center;
    gap: 22px;
  }
  .front-mark__square {
    width: 58px; height: 58px;
    background: var(--navy-soft);
  }
  .front-mark__name {
    color: var(--navy-soft);
    font-weight: 800;
    font-size: 40px;
    line-height: 1.1;
    letter-spacing: 1px;
  }

  .back-mark {
    position: absolute;
    left: 36px;
    top: 150px;
    width: 320px;
    display: flex;
    align-items: center;
    justify-content: center;
    gap: 14px;
  }
  .back-mark__square {
    width: 40px; height: 40px;
    background: var(--red);
    flex: none;
  }
  .back-mark__name {
    color: var(--navy);
    font-weight: 800;
    font-size: 27px;
    line-height: 1.1;
    letter-spacing: 0.5px;
  }

  .divider {
    position: absolute;
    left: 371px;
    top: 94px;
    width: 2px;
    height: 222px;
    background: var(--red);
  }
  .details {
    position: absolute;
    left: 400px;
    top: 92px;
    color: var(--ink);
  }
  .details__name {
    font-weight: 700;
    font-size: 34px;
    line-height: 1;
    color: var(--navy);
  }
  .details__name span { color: var(--red); }
  .details__role { font-size: 19px; margin-top: 10px; }
  .details__address { font-size: 19px; line-height: 29px; margin-top: 14px; }
  .contact { list-style: none; margin-top: 12px; }
  .contact li {
    display: flex;
    align-items: center;
    gap: 9px;
    font-size: 19px;
    line-height: 28.5px;
  }
  .contact svg { width: 16px; height: 16px; fill: var(--red); flex: none; }
</style>
</head>
<body>
  <section class="card card--front">
    <div class="front-mark">
      <div class="front-mark__square"></div>
      <div class="front-mark__name">VOLTLINE<br>COMMERCIAL POWER</div>
    </div>
  </section>

  <section class="card card--back">
    <div class="back-mark">
      <div class="back-mark__square"></div>
      <div class="back-mark__name">VOLTLINE<br>COMMERCIAL POWER</div>
    </div>

    <div class="divider"></div>

    <div class="details">
      <h1 class="details__name">Daniel <span>Rourke</span></h1>
      <p class="details__role">Managing Director</p>
      <p class="details__address">Your address, City<br>State, Zip 1234</p>
      <ul class="contact">
        <li>
          <svg viewBox="0 0 16 16" aria-hidden="true"><path d="M1 6c0-2 3-3 7-3s7 1 7 3v1h-3.5V5.5h-7V7H1zM4 8h8l2 5H2z"/></svg>
          123 456 789
        </li>
        <li>
          <svg viewBox="0 0 16 16" aria-hidden="true"><path d="M1 3h14v10H1zM2.2 4.2v.4L8 9l5.8-4.4v-.4z"/></svg>
          info@yourmail.com
        </li>
        <li>
          <svg viewBox="0 0 16 16" aria-hidden="true"><circle cx="8" cy="8" r="7"/><path d="M5 4h3v3H5zM9 9h3v3H9z" fill="#fff"/></svg>
          www.yourwebsite.com
        </li>
      </ul>
    </div>
  </section>
</body>
</html>
```